Business Card Design (NEW FILES)

ATTENTION: New vector files are available. Please update your design to reflect/use the new (better resolution) logo images.

Seeking a unique and professional business card design for a commercial drone photography/videography business. The layout should feature
the logo (attached) and include the following information:
Owen Tarrick
614-502-7738
www.skylarkreelworks.example
NRD Certified Remote Pilot

Owen Tarrick

```html
<!DOCTYPE html>
<html lang="en">
<head>
<meta charset="utf-8">
<title>Skylark Reelworks – Business Card</title>
<link rel="stylesheet" href="https://fonts.googleapis.com/css2?family=Lato:wght@400;700;900&display=swap">
<style>
  :root {
    --backdrop: #8f8f8f;
    --navy: #131a45;
    --orange: #e8894a;
    --white: #ffffff;
    --ink: #1c2250;
    --purple: #6a3fa0;
    --magenta: #c2338f;
    --red: #d8302f;
    --amber: #f0a030;
    --green: #8cc63f;
    --teal: #1fb5b0;
  }
  * { box-sizing: border-box; margin: 0; padding: 0; }
  html, body { width: 1200px; height: 1200px; overflow: hidden; }
  body {
    background: var(--backdrop);
    font-family: "Lato", sans-serif;
    position: relative;
  }
  .card {
    position: absolute;
    left: 281px;
    width: 641px;
    height: 366px;
    border-radius: 20px;
    overflow: hidden;
  }
  .card--front { top: 195px; background: var(--white); }
  .card--back { top: 639px; background: var(--navy); }

  .contact-block {
    position: absolute;
    right: 362px;
    top: 90px;
    text-align: right;
    color: var(--ink);
  }
  .contact-block__name {
    font-weight: 900;
    font-size: 29px;
    letter-spacing: 0.3px;
    line-height: 1;
  }
  .contact-block__role {
    color: var(--orange);
    font-size: 16px;
    margin-top: 6px;
  }
  .spectrum-rule {
    display: flex;
    width: 202px;
    height: 2px;
    margin: 12px 0 14px auto;
    gap: 2px;
  }
  .spectrum-rule span { flex: 1; }
  .contact-list { list-style: none; }
  .contact-list li {
    display: flex;
    justify-content: flex-end;
    align-items: center;
    gap: 10px;
    font-size: 15px;
    height: 22.5px;
  }
  .contact-list svg { width: 12px; height: 12px; fill: var(--orange); }

  .brand-name {
    position: absolute;
    left: 326px;
    top: 132px;
    color: var(--ink);
    font-weight: 400;
    font-size: 34px;
    line-height: 1.05;
    letter-spacing: 1px;
    text-transform: uppercase;
  }
  .brand-name__mark {
    display: inline-block;
    width: 16px; height: 16px;
    border-radius: 50%;
    background: var(--orange);
    margin-left: 8px;
    vertical-align: middle;
  }

  .insured-band {
    position: absolute;
    left: 0; right: 0;
    bottom: 0;
    height: 46px;
    background: var(--navy);
    border-top: 4px solid var(--orange);
    box-shadow: 0 -2px 0 var(--white);
  }
  .insured-band__text {
    position: absolute;
    left: 337px;
    transform: translateX(-50%);
    top: 10px;
    font-weight: 900;
    font-size: 18px;
    letter-spacing: 3px;
    color: var(--white);
    white-space: nowrap;
  }
  .insured-band__text em { font-style: normal; color: var(--orange); }
  .cert-badge {
    position: absolute;
    left: 535px;
    top: 279px;
    width: 80px; height: 80px;
    border-radius: 50%;
    background: var(--navy);
    border: 3px solid var(--white);
  }

  .back-brand {
    position: absolute;
    left: 0; right: 0;
    top: 142px;
    text-align: center;
    color: var(--white);
    font-weight: 400;
    font-size: 46px;
    letter-spacing: 2px;
    text-transform: uppercase;
    line-height: 1.05;
  }
  .back-brand .brand-name__mark { width: 20px; height: 20px; }
</style>
</head>
<body>
  <section class="card card--front">
    <div class="contact-block">
      <div class="contact-block__name">OWEN TARRICK</div>
      <div class="contact-block__role">Owner</div>
      <div class="spectrum-rule">
        <span style="background:var(--purple)"></span>
        <span style="background:var(--magenta)"></span>
        <span style="background:var(--red)"></span>
        <span style="background:var(--amber)"></span>
        <span style="background:var(--green)"></span>
        <span style="background:var(--teal)"></span>
      </div>
      <ul class="contact-list">
        <li>614-502-7738
          <svg viewBox="0 0 24 24"><path d="M6.6 10.8a15.1 15.1 0 0 0 6.6 6.6l2.2-2.2c.3-.3.7-.4 1-.2 1.1.4 2.3.6 3.6.6.6 0 1 .4 1 1V20c0 .6-.4 1-1 1A17 17 0 0 1 3 4c0-.6.4-1 1-1h3.5c.6 0 1 .4 1 1 0 1.3.2 2.5.6 3.6.1.3 0 .7-.2 1z"/></svg>
        </li>
        <li>owen@skylarkreelworks.example
          <svg viewBox="0 0 24 24"><path d="M2 5h20v14H2z M2 5l10 8 10-8" stroke="#fff" stroke-width="1.5"/></svg>
        </li>
        <li>skylarkreelworks.example
          <svg viewBox="0 0 24 24"><circle cx="12" cy="12" r="10"/></svg>
        </li>
      </ul>
    </div>

    <div class="brand-name">Skylark<br>Reelworks<span class="brand-name__mark"></span></div>

    <div class="insured-band">
      <div class="insured-band__text">FULLY <em>INSURED</em></div>
    </div>
    <div class="cert-badge" role="img" aria-label="NRD certified remote pilot badge"></div>
  </section>

  <section class="card card--back">
    <div class="back-brand">Skylark<br>Reelworks<span class="brand-name__mark"></span></div>
  </section>
</body>
</html>
```